Push notification screens at app start up

We have an existing news publication app platform and are adding categories to push notifications.

We need two screens designed (each for Zorbel, Quillet and Android for a total of 6d) that show when the app is first launched.

The workflow of our app:
0. app launch screen while webservices run (no work needed)
1. information screen to the user promoting the benefits of push notification with "Next" button. (see concept attached)
2. Push categories selection screen. This will have list of category types, with on/off switch.

"Select the categories that you wish to receive occasional notices:
Breaking News (on/off switch)
Local News (on/off switch)
Sports (on/off switch)
Local Events (on/off switch)
Weather Alerts (on/off switch)
Local Deals (on/off switch)"

"Enable these categories on the next screen."
"Next" button

Background:
When I was looking around at app designs, I came across this one (http://www.plinthworks.example/design/7719034) and I really liked it. We obviously have different features on our screen, but I’d like to have this same feel. The colors used in this design are perfect.

UPDATE: I do not mean to limit your design to match the layout as the one mentioned above. Please use your creativity for the layout.

Our standard font in Helvetica Neue.

Notes:
- our app is developed for all phone devices from Zorbel 4 to Zorbel 6, so designs should be thoughtful of vertical scrolling if needed.
- our app is developed for Quillets, so we'll need designs completed as well. (We can finalize Zorbel design first, then translate the design to Quillet.)
- our app is developed for Android phones (not tablets), so we'll need designs completed as well. (We can finalize iOS design first, then translater to Android UI design guidelines).

We hope to establish a good on-going relationship with the designer for as-needed work in the future.

News

• Helvetica Neue

• Clean designs. No clutter.
• We would likely go with the standard on/off switches for both iOS and Android, but are open to small custom variations.

```html
<!DOCTYPE html>
<html lang="en">
<head>
<meta charset="utf-8">
<title>Notifications – onboarding</title>
<link rel="stylesheet" href="https://fonts.googleapis.com/css2?family=Roboto:wght@300;400;500;700&display=swap">
<style>
  :root {
    --screen-bg: #000000;
    --status-text: #ffffff;
    --card-bg: #e8e8e8;
    --accent-blue: #1f6ff2;
    --title-text: #3a3a3a;
    --body-text: #5a5a5a;
    --button-text: #ffffff;
  }
  * { margin: 0; padding: 0; box-sizing: border-box; }
  html, body {
    width: 675px; height: 1200px; overflow: hidden;
    background: var(--screen-bg);
    font-family: "Roboto", "Helvetica Neue", Helvetica, Arial, sans-serif;
  }
  .screen { position: relative; width: 675px; height: 1200px; background: var(--screen-bg); }

  .status-bar {
    position: absolute; top: 0; left: 0; width: 100%; height: 45px;
    color: var(--status-text); font-size: 24px; font-weight: 400;
  }
  .status-bar .carrier { position: absolute; left: 8px; top: 9px; display: flex; align-items: center; gap: 8px; }
  .status-bar .signal { display: flex; gap: 3px; }
  .status-bar .signal span { width: 11px; height: 11px; border-radius: 50%; background: var(--status-text); }
  .status-bar .signal span.empty { background: none; border: 1.5px solid var(--status-text); }
  .status-bar .time { position: absolute; left: 0; right: 0; top: 9px; text-align: center; font-weight: 500; }
  .status-bar .power { position: absolute; right: 10px; top: 9px; display: flex; align-items: center; gap: 8px; }

  .permission-card {
    position: absolute; left: 27px; top: 146px; width: 621px; height: 720px;
    background: var(--card-bg); border-radius: 22px; text-align: center;
  }
  .card-badge {
    position: absolute; left: 50%; top: -79px; width: 158px; height: 158px; margin-left: -79px;
    border-radius: 50%; background: var(--accent-blue);
    display: flex; align-items: center; justify-content: center;
  }
  .card-title {
    position: absolute; top: 195px; left: 0; right: 0;
    font-size: 43px; font-weight: 700; color: var(--title-text);
  }
  .card-copy {
    position: absolute; left: 0; right: 0;
    font-size: 26px; line-height: 34.6px; font-weight: 300; color: var(--body-text);
  }
  .card-copy.intro { top: 298px; }
  .card-copy.reassure { top: 545px; }

  .next-button {
    position: absolute; left: 27px; top: 916px; width: 621px; height: 97px;
    border: none; border-radius: 14px; background: var(--accent-blue);
    color: var(--button-text); font-family: inherit; font-size: 40px; font-weight: 700;
    letter-spacing: 1px;
  }
</style>
</head>
<body>
<main class="screen">
  <header class="status-bar">
    <div class="carrier">
      <div class="signal"><span></span><span></span><span></span><span class="empty"></span><span class="empty"></span></div>
      <span>VELLO</span>
      <svg width="26" height="20" viewBox="0 0 26 20" aria-label="Wi-Fi">
        <path d="M13 18 L9 13 A6 6 0 0 1 17 13 Z" fill="#fff"/>
        <path d="M4.5 9 A12 12 0 0 1 21.5 9" stroke="#fff" stroke-width="2.6" fill="none"/>
        <path d="M1 5 A17 17 0 0 1 25 5" stroke="#fff" stroke-width="2.6" fill="none"/>
      </svg>
    </div>
    <div class="time">4:21 PM</div>
    <div class="power">
      <span>100%</span>
      <svg width="54" height="24" viewBox="0 0 54 24" aria-label="Battery full">
        <rect x="1" y="2" width="46" height="20" rx="4" fill="none" stroke="#fff" stroke-width="2"/>
        <rect x="4" y="5" width="40" height="14" rx="2" fill="#fff"/>
        <rect x="49" y="8" width="4" height="8" rx="1.5" fill="#fff"/>
      </svg>
    </div>
  </header>

  <section class="permission-card">
    <div class="card-badge">
      <svg width="120" height="80" viewBox="0 0 120 80" aria-label="Megaphone">
        <g fill="none" stroke="#fff" stroke-width="5" stroke-linejoin="round" stroke-linecap="round">
          <path d="M8 28 L22 28 L58 10 L58 66 L22 48 L8 48 Z"/>
          <path d="M22 28 L22 48"/>
          <path d="M16 48 L20 68 L30 68 L28 52"/>
          <path d="M70 28 A14 14 0 0 1 70 48"/>
          <path d="M80 20 A26 26 0 0 1 80 56"/>
          <path d="M90 12 A38 38 0 0 1 90 64"/>
        </g>
      </svg>
    </div>
    <h1 class="card-title">Notifications</h1>
    <p class="card-copy intro">
      By enabling push notifications, you can<br>
      keep up to date with occasional<br>
      notifications related to items you care<br>
      about. Select the categories on the<br>
      next screen and then authorize the<br>
      push notifications.
    </p>
    <p class="card-copy reassure">
      If you ever change your mind, you can<br>
      adjust these options in the Settings<br>
      menu of this app.
    </p>
  </section>

  <button class="next-button" type="button">NEXT</button>
</main>
</body>
</html>
```